Real Estate Brokerage Stationery Designs

I am looking to have presentation folders with business card slots on both sides along with pockets on both sides. I've attached logos, website colors along with current business card designs.

I am looking for envelope designs both big and small. Possibly new business card designs, notepad templates for big and small notepads. Letterhead designs. Pop socket designs. Realtors name badge designs.

www.brightholdrealty.example

```html
<!DOCTYPE html>
<html lang="en">
<head>
<meta charset="utf-8">
<title>Brighthold Realty Presentation Folder</title>
<link rel="stylesheet" href="https://fonts.googleapis.com/css2?family=Open+Sans:wght@400;600;700&display=swap">
<style>
  :root {
    --sky-top: #cfe4fb;
    --sky-bottom: #7fb6ee;
    --blue-light: #5d9fe0;
    --blue-mid: #3f82cf;
    --blue-deep: #1f5fae;
    --navy: #17458f;
    --ink: #1b2a44;
    --paper: #ffffff;
    --paper-grey: #e9ebee;
    --strip-grey: #d3d6db;
    --faint: #b9bcc2;
    --photo-a: #c9a77a;
    --photo-b: #4f6a5a;
    --photo-sky: #8fb9e2;
  }
  * { margin: 0; padding: 0; box-sizing: border-box; }
  html, body { width: 1200px; height: 1080px; overflow: hidden; }
  body {
    background: linear-gradient(180deg, var(--sky-top), var(--sky-bottom));
    font-family: "Open Sans", Arial, sans-serif;
    position: relative;
  }
  .spread {
    position: absolute;
    left: 225px;
    width: 750px;
    height: 500px;
    display: flex;
    box-shadow: 0 14px 30px rgba(20, 60, 120, 0.25);
  }
  .spread--outside { top: 20px; }
  .spread--inside { top: 560px; }
  .panel { position: relative; width: 375px; height: 500px; overflow: hidden; }
  .panel svg.panel__art { position: absolute; inset: 0; }
  .panel__text { position: absolute; left: 0; right: 0; text-align: center; }

  .brand-name {
    font-weight: 700;
    color: var(--navy);
    font-size: 30px;
    letter-spacing: 1px;
    line-height: 1.15;
  }
  .brand-name span { display: block; font-size: 18px; letter-spacing: 4px; }
  .brand-mark {
    display: block; width: 16px; height: 16px; margin: 0 auto 10px;
    background: var(--navy);
  }
  .front__brand { top: 120px; }
  .url { font-weight: 700; color: var(--navy); font-size: 13px; }
  .front__url { top: 467px; }

  .deals__tab {
    position: absolute; left: 137px; top: 292px; width: 100px; height: 20px;
    background: var(--blue-deep); color: var(--paper); font-weight: 700;
    font-size: 11px; line-height: 20px; text-align: center; border-radius: 2px;
  }
  .deals__list {
    top: 320px; color: var(--paper); font-weight: 700; font-size: 11px; line-height: 18px;
  }
  .deals__list b { display: inline-block; width: 6px; height: 6px; border-radius: 50%;
    background: var(--paper); margin: 0 6px 1px; vertical-align: middle; }
  .address { top: 404px; color: var(--paper); font-weight: 700; font-size: 10px; }
  .contacts { top: 468px; color: var(--ink); font-size: 9.5px; font-weight: 600; }
  .contacts span { margin: 0 6px; }

  .inside__brand { top: 165px; }
  .inside__brand .brand-name { color: var(--faint); }
  .inside__brand .brand-mark { background: var(--faint); }

  .card {
    position: absolute; top: 378px; left: 95px; width: 185px; height: 96px;
    background: var(--paper); box-shadow: 0 2px 6px rgba(0,0,0,0.25); display: flex;
  }
  .card__info { width: 95px; padding: 12px 6px 0 8px; }
  .card__name-brand { font-weight: 700; color: var(--navy); font-size: 9px; line-height: 1.2; }
  .card__services { font-size: 5px; color: var(--ink); margin-top: 6px; line-height: 1.4; }
  .card__badges { display: flex; gap: 3px; margin-top: 6px; }
  .card__badges i { width: 10px; height: 8px; background: var(--ink); }
  .card__portrait {
    position: relative; flex: 1;
    background: linear-gradient(180deg, #dfe3e8, #9aa3ad);
  }
  .card__person {
    position: absolute; bottom: 0; left: 0; right: 0; height: 24px; background: var(--ink);
    color: var(--paper); font-size: 7px; font-weight: 700; text-align: right; padding: 4px 6px 0;
    line-height: 1.2;
  }
  .card__person small { display: block; font-size: 5px; font-weight: 600; }
</style>
</head>
<body>

<section class="spread spread--outside">
  <!-- Back cover -->
  <article class="panel panel--back">
    <svg class="panel__art" viewBox="0 0 375 500" width="375" height="500">
      <defs>
        <linearGradient id="backBlue" x1="0" y1="0" x2="0" y2="1">
          <stop offset="0" stop-color="var(--blue-light)"/>
          <stop offset="1" stop-color="var(--blue-mid)"/>
        </linearGradient>
        <linearGradient id="backPhoto" x1="0" y1="0" x2="1" y2="1">
          <stop offset="0" stop-color="var(--photo-sky)"/>
          <stop offset="0.55" stop-color="var(--photo-a)"/>
          <stop offset="1" stop-color="var(--photo-b)"/>
        </linearGradient>
        <linearGradient id="thumb" x1="0" y1="0" x2="1" y2="1">
          <stop offset="0" stop-color="var(--photo-a)"/>
          <stop offset="1" stop-color="var(--photo-b)"/>
        </linearGradient>
      </defs>
      <rect class="back__ground" width="375" height="500" fill="url(#backBlue)"/>
      <path class="back__photo" role="img" aria-label="Photo of a single-storey home with a double garage and palm trees"
            d="M0,0 L340,0 C300,70 250,110 190,150 C120,195 50,200 0,300 Z" fill="url(#backPhoto)"/>
      <path class="back__wave-edge" d="M340,0 C300,70 250,110 190,150 C120,195 50,200 0,300"
            fill="none" stroke="var(--paper)" stroke-width="4"/>
      <g class="back__thumbs">
        <g transform="translate(85 235) rotate(-45)">
          <rect x="-26" y="-26" width="52" height="52" rx="5" fill="var(--paper)"/>
          <rect role="img" aria-label="Photo of a garden and lawn" x="-22" y="-22" width="44" height="44" rx="3" fill="url(#thumb)"/>
        </g>
        <g transform="translate(187 225) rotate(-45)">
          <rect x="-26" y="-26" width="52" height="52" rx="5" fill="var(--paper)"/>
          <rect role="img" aria-label="Photo of a bedroom interior" x="-22" y="-22" width="44" height="44" rx="3" fill="url(#thumb)"/>
        </g>
        <g transform="translate(289 215) rotate(-45)">
          <rect x="-26" y="-26" width="52" height="52" rx="5" fill="var(--paper)"/>
          <rect role="img" aria-label="Photo of a home entrance" x="-22" y="-22" width="44" height="44" rx="3" fill="url(#thumb)"/>
        </g>
      </g>
      <rect class="back__address-band" x="0" y="385" width="375" height="65" fill="var(--blue-deep)"/>
      <path d="M170,392 a6,6 0 1 1 12,0 c0,5 -6,10 -6,10 c0,0 -6,-5 -6,-10 z" fill="var(--paper)"/>
      <circle cx="176" cy="392" r="2" fill="var(--blue-deep)"/>
      <rect class="back__strip" x="0" y="450" width="375" height="50" fill="var(--paper)"/>
      <rect x="0" y="450" width="375" height="3" fill="var(--strip-grey)"/>
    </svg>
    <div class="deals__tab">Deals In:</div>
    <p class="panel__text deals__list">
      <b></b>Residential Real Estate<b></b>Commercial Real Estate<br>
      <b></b>Property Management<b></b>Investments
    </p>
    <p class="panel__text address">2400 Harbor View Dr, Ste 310, Coral Bend, FL 33000</p>
    <p class="panel__text contacts">
      <span>&#9742; 555-010-2715</span><span>&#9742; 555-010-0455</span><br>
      <span>&#9993; contact@brightholdrealty.example</span><span>www.brightholdrealty.example</span>
    </p>
  </article>

  <!-- Front cover -->
  <article class="panel panel--front">
    <svg class="panel__art" viewBox="0 0 375 500" width="375" height="500">
      <defs>
        <linearGradient id="frontBlue" x1="0" y1="0" x2="0" y2="1">
          <stop offset="0" stop-color="var(--blue-light)"/>
          <stop offset="1" stop-color="var(--blue-deep)"/>
        </linearGradient>
        <linearGradient id="frontPhoto" x1="0" y1="0" x2="1" y2="1">
          <stop offset="0" stop-color="#2c4a66"/>
          <stop offset="0.5" stop-color="var(--photo-a)"/>
          <stop offset="1" stop-color="#6b4a32"/>
        </linearGradient>
        <linearGradient id="greyStrip" x1="0" y1="0" x2="0" y2="1">
          <stop offset="0" stop-color="var(--paper)"/>
          <stop offset="1" stop-color="var(--strip-grey)"/>
        </linearGradient>
      </defs>
      <rect class="front__ground" width="375" height="500" fill="url(#frontBlue)"/>
      <path class="front__photo" role="img" aria-label="Photo of a two-storey villa with a lit garage at dusk"
            d="M0,450 L0,410 C70,320 150,380 230,320 C290,275 330,250 375,210 L375,450 Z" fill="url(#frontPhoto)"/>
      <path class="front__wave-edge" d="M0,410 C70,320 150,380 230,320 C290,275 330,250 375,210"
            fill="none" stroke="var(--paper)" stroke-width="4"/>
      <rect class="front__strip" x="0" y="450" width="375" height="50" fill="url(#greyStrip)"/>
    </svg>
    <div class="panel__text front__brand">
      <i class="brand-mark"></i>
      <p class="brand-name">BRIGHTHOLD<span>REALTY</span></p>
    </div>
    <p class="panel__text url front__url">www.brightholdrealty.example</p>
  </article>
</section>

<section class="spread spread--inside">
  <article class="panel panel--inside-left">
    <svg class="panel__art" viewBox="0 0 375 500" width="375" height="500">
      <rect width="375" height="500" fill="var(--paper)"/>
      <rect class="pocket" x="0" y="360" width="375" height="140" fill="var(--blue-mid)"/>
      <rect x="0" y="360" width="375" height="2" fill="var(--blue-deep)"/>
    </svg>
    <div class="panel__text inside__brand">
      <i class="brand-mark"></i>
      <p class="brand-name">BRIGHTHOLD<span>REALTY</span></p>
    </div>
    <div class="card">
      <div class="card__info">
        <p class="card__name-brand">BRIGHTHOLD<br>REALTY</p>
        <p class="card__services">Residential Real Estate | Commercial Real Estate<br>Property Management | Investments</p>
        <div class="card__badges"><i></i><i></i></div>
      </div>
      <div class="card__portrait" role="img" aria-label="Portrait photo of the broker">
        <p class="card__person">MARCUS DELANE<small>BROKER</small></p>
      </div>
    </div>
  </article>

  <article class="panel panel--inside-right">
    <svg class="panel__art" viewBox="0 0 375 500" width="375" height="500">
      <rect width="375" height="500" fill="var(--paper-grey)"/>
      <rect class="pocket" x="0" y="360" width="375" height="140" fill="var(--blue-mid)"/>
      <rect x="0" y="360" width="375" height="2" fill="var(--blue-deep)"/>
    </svg>
    <div class="panel__text inside__brand">
      <i class="brand-mark"></i>
      <p class="brand-name">BRIGHTHOLD<span>REALTY</span></p>
    </div>
    <div class="card">
      <div class="card__info">
        <p class="card__name-brand">BRIGHTHOLD<br>REALTY</p>
        <p class="card__services">Residential Real Estate | Commercial Real Estate<br>Property Management | Investments</p>
        <div class="card__badges"><i></i><i></i></div>
      </div>
      <div class="card__portrait" role="img" aria-label="Portrait photo of the realtor">
        <p class="card__person">EVAN MORALES<small>REALTOR</small></p>
      </div>
    </div>
  </article>
</section>

</body>
</html>
```